Wordpress Website design partner needed for an Arabic Language Institute for English Speakers

We are an online Arabic Language institute, targeting English Speakers around the world and we provide online courses and private group and one on one classes
We are looking for a total of 5 pages designed.
The Design should be mobile-first, and then provide PC for any differences.
I am looking for a consistent design with a lot of white space and in line with our Logo colours.
Images used should be around the theme of Arabic Language/Islamic in Nature, so please do not use any illustrations or images of animals or human beings except for silhouettes or images without faces visible, such as someone facing other way or below torso or hands etc.
The website will eventually be prepared for Wordpress using Divi.
I will provide a very structured outline of what elements and modules each page should have. Therefore I am looking for someone that has an eye for detail and is precise in executing requirements.
I decided to post on this site because I am looking for a long-term partner that can take care of any of our design needs as they come up.
More details to follow
I will do abit more research tomorrow to suggest sample sites
Updates
Target Market(s)
English speakers that want to learn Arabic for Religous purposes such as understanding the Quran
Industry/Entity Type
Education
Colors
Designer to choose colors to be used in the design.
Requirements
Must have
- Mobile First, and design for PC for changes
- Consistency
- Plenty of White Space
- Colour Palette based on Logo
- Colour and Transparent/White Header for when scrolling
- Big Call to Action buttons with contrasting colors
- A consistent footer for all pages with
- -Social Media Icons
- -Contact us
- -Sitemap
- -Copyright
- -Logo
- Anything with a hashtag (#) beforehand in the Doc file means it should be a module like the modules used in Divi Theme, Please check the following website for an explanation of what each module consists of and some examples of it in use. https://www.pelmorashowcase.net/pelmora-blocks-guide/
Nice to have
- Parallax Effect
Should not have
- illustrations or images of animals or human beings except for silhouettes or images without faces visible, such as someone facing other way or below torso or hands etc.

```html
<!DOCTYPE html>
<html lang="en">
<head>
<meta charset="utf-8">
<title>Contact Us – Al-Bayan Arabic Academy</title>
<link href="https://fonts.googleapis.com/css2?family=IBM+Plex+Sans:wght@400;500;600;700&display=swap" rel="stylesheet">
<style>
:root{
  --blue:#114b99;
  --teal:#2694a9;
  --ink:#111;
  --field:#f4f1f1;
  --field-line:#b9b6b6;
  --soft:#f4f1f1;
  --footer:#222222;
  --white:#fff;
}
*{box-sizing:border-box;margin:0;padding:0}
html,body{width:687px;height:1200px;overflow:hidden;background:var(--white)}
body{position:relative;font-family:"IBM Plex Sans",Arial,sans-serif;color:var(--ink)}

/* hero */
.hero{position:absolute;left:0;top:0;width:687px;height:211px;background:var(--blue);overflow:hidden}
.hero-art{position:absolute;left:0;top:60px;width:430px;height:151px;background:radial-gradient(ellipse at 30% 100%,#1c5aa8 0%,#1552a0 40%,rgba(17,75,153,0) 75%)}
.nav a{position:absolute;color:var(--white);font-size:8.5px;font-weight:500;text-decoration:none;letter-spacing:.2px}
.nav .sep{position:absolute;width:1px;height:18px;background:rgba(255,255,255,.7)}
.nav a.current{color:var(--teal);text-decoration:underline;text-underline-offset:2px}
.brand-top{position:absolute;left:306px;top:42px;width:76px;text-align:center;color:var(--white);font-size:10px;font-weight:600;line-height:1.2;letter-spacing:.5px}
.login{position:absolute;left:557px;top:37px;width:53px;height:23px;border:1.5px solid var(--white);border-radius:12px;color:var(--white);font-size:7.5px;font-weight:600;display:flex;align-items:center;justify-content:center}
.hero h1{position:absolute;left:0;width:687px;top:129px;text-align:center;color:var(--white);font-size:23px;font-weight:700;letter-spacing:.5px}

/* contact form */
.form-title{position:absolute;left:112px;top:248px;font-size:17px;font-weight:700;letter-spacing:.3px}
.field{position:absolute;background:var(--field);border:1px solid var(--field-line);font-size:7.5px;padding:9px 10px}
.submit{position:absolute;left:503px;top:424px;width:71px;height:29px;border-radius:15px;background:var(--teal);color:var(--white);font-size:10px;font-weight:600;display:flex;align-items:center;justify-content:center;letter-spacing:.3px}

/* features */
.features{position:absolute;left:0;top:488px;width:687px;height:353px;background:var(--soft)}
.features h2{position:absolute;left:0;width:687px;top:23px;text-align:center;font-size:15.5px;font-weight:700;letter-spacing:.3px}
.features .rule{position:absolute;left:329px;top:50px;width:30px;height:2px;background:var(--teal)}
.acc{position:absolute;left:95px;width:499px;background:var(--white);border:1px solid #cfcccc;font-size:8.5px}
.acc .q{position:absolute;left:11px;top:8px}
.acc svg{position:absolute;right:12px;top:10px}
.acc.open .q{font-weight:600}
.acc .a{position:absolute;left:17px;top:35px;right:18px;font-size:7.6px;line-height:11px;color:#333}

/* cards */
.card{position:absolute;top:869px;width:171px;height:77px;background:var(--teal);color:var(--white);text-align:center}
.card .lbl{position:absolute;left:0;width:100%;top:39px;font-size:8px;font-weight:600;letter-spacing:.3px}
.card .val{position:absolute;left:0;width:100%;top:51px;font-size:10px;font-weight:600}
.card svg{position:absolute;left:50%;transform:translateX(-50%);top:14px}
.dots{position:absolute;left:0;width:100%;top:17px;display:flex;justify-content:center;gap:7px}
.dots span{width:9px;height:9px;border-radius:50%;background:var(--white)}

/* footer */
.footer{position:absolute;left:0;top:975px;width:687px;height:225px;background:var(--footer);color:var(--white)}
.footer h3{position:absolute;font-size:8px;font-weight:600;letter-spacing:.3px}
.f-item{position:absolute;display:flex;align-items:center;gap:9px;font-size:7.8px;line-height:10px}
.f-item .ic{width:20px;height:20px;border-radius:50%;background:var(--teal);display:flex;align-items:center;justify-content:center;flex:none}
.f-item b{font-weight:600;font-size:7.2px;display:block}
.f-item strong{font-weight:500;font-size:8.3px}
.frame{position:absolute;left:246px;top:33px;width:195px;height:96px;border:1px solid #9a9a9a;border-top:none}
.frame-gap{position:absolute;left:301px;top:121px;width:85px;height:12px;background:var(--footer)}
.brand-foot{position:absolute;left:286px;top:98px;width:115px;text-align:center;font-weight:600;font-size:11px;letter-spacing:1.5px;line-height:1.3}
.brand-foot small{display:block;font-size:5.5px;letter-spacing:2px}
.f-links{position:absolute;left:0;width:687px;top:146px;display:flex;justify-content:center;gap:10px;font-size:8px;font-weight:600;letter-spacing:.2px}
.f-line{position:absolute;left:75px;top:181px;width:537px;height:1px;background:#555}
.copy{position:absolute;left:0;width:687px;top:202px;text-align:center;font-size:6.5px;color:#ddd}
</style>
</head>
<body>

<header class="hero">
  <div class="hero-art" role="img" aria-label="Faint silhouette of a mosque dome and minaret in deep blue tones"></div>
  <nav class="nav">
    <a style="left:180px;top:43px">HOME</a>
    <span class="sep" style="left:224px;top:39px"></span>
    <a style="left:241px;top:43px">ABOUT US</a>
    <a style="left:395px;top:43px">COURSES</a>
    <span class="sep" style="left:450px;top:39px"></span>
    <a class="current" style="left:467px;top:43px">CONTACT US</a>
  </nav>
  <div class="brand-top">AL-BAYAN</div>
  <div class="login">LOGIN</div>
  <h1>CONTACT US</h1>
</header>

<section class="contact-form">
  <h2 class="form-title">GET IN TOUCH</h2>
  <div class="field" style="left:112px;top:285px;width:227px;height:27px">NAME</div>
  <div class="field" style="left:347px;top:285px;width:227px;height:27px">E MAIL ADDRESS</div>
  <div class="field" style="left:112px;top:320px;width:462px;height:90px">MESSAGE</div>
  <div class="submit">SUBMIT</div>
</section>

<section class="features">
  <h2>FEATURES</h2>
  <div class="rule"></div>
  <div class="acc" style="top:79px;height:27px"><span class="q">At vero eos et accusamus et iusto</span>
    <svg width="9" height="6" viewBox="0 0 9 6"><path d="M1 1l3.5 3.5L8 1" fill="none" stroke="#555" stroke-width="1.3"/></svg></div>
  <div class="acc" style="top:113px;height:27px"><span class="q">On the other hand, we denounce with righteous</span>
    <svg width="9" height="6" viewBox="0 0 9 6"><path d="M1 1l3.5 3.5L8 1" fill="none" stroke="#555" stroke-width="1.3"/></svg></div>
  <div class="acc" style="top:147px;height:27px"><span class="q">Pleasures to secure other greater pleasures</span>
    <svg width="9" height="6" viewBox="0 0 9 6"><path d="M1 1l3.5 3.5L8 1" fill="none" stroke="#555" stroke-width="1.3"/></svg></div>
  <div class="acc" style="top:181px;height:27px"><span class="q">Quis nostrum exercitationem ullam corporis</span>
    <svg width="9" height="6" viewBox="0 0 9 6"><path d="M1 1l3.5 3.5L8 1" fill="none" stroke="#555" stroke-width="1.3"/></svg></div>
  <div class="acc open" style="top:215px;height:110px"><span class="q">Many desktop publishing packages and web pag</span>
    <svg width="9" height="6" viewBox="0 0 9 6"><path d="M1 5l3.5-3.5L8 5" fill="none" stroke="#111" stroke-width="1.4"/></svg>
    <p class="a">Lorem ipsum dolor sit amet, consectetur adipiscing elit, sed do eiusmod tempor incididunt ut labore et dolore magna aliqua. Ut enim ad minim veniam, quis nostrud exercitation ullamco laboris nisi ut aliquip ex ea commodo consequat. Duis aute irure dolor in reprehenderit in voluptate velit esse cillum dolore eu fugiat nulla pariatur. Excepteur sint occaecat cupidatat non proident, sunt in culpa qui officia deserunt mollit anim id est laborum. Nemo enim ipsam voluptatem quia voluptas sit aspernatur aut odit aut fugit, sed quia consequuntur magni dolores</p>
  </div>
</section>

<section class="contact-cards">
  <div class="card" style="left:75px">
    <svg width="17" height="13" viewBox="0 0 17 13"><rect x="0" y="0" width="17" height="13" rx="1.5" fill="#fff"/><path d="M1 1.5l7.5 6 7.5-6" fill="none" stroke="#2694a9" stroke-width="1.4"/></svg>
    <div class="lbl">EMAIL US</div><div class="val">info@albayanacademy.com</div>
  </div>
  <div class="card" style="left:257px">
    <svg width="14" height="14" viewBox="0 0 24 24"><path fill="#fff" d="M6.6 10.8a15.1 15.1 0 0 0 6.6 6.6l2.2-2.2c.3-.3.7-.4 1-.2 1.1.4 2.3.6 3.6.6.6 0 1 .4 1 1V20c0 .6-.4 1-1 1A17 17 0 0 1 3 4c0-.6.4-1 1-1h3.5c.6 0 1 .4 1 1 0 1.3.2 2.5.6 3.6.1.3 0 .7-.2 1z"/></svg>
    <div class="lbl">CALL US</div><div class="val">555.014.2290</div>
  </div>
  <div class="card" style="left:441px">
    <div class="dots"><span></span><span></span><span></span></div>
    <div class="lbl" style="top:43px">FOLLOW US</div>
  </div>
</section>

<footer class="footer">
  <h3 style="left:78px;top:33px">CONTACT US</h3>
  <div class="f-item" style="left:75px;top:57px">
    <span class="ic"><svg width="9" height="9" viewBox="0 0 24 24"><path fill="#fff" d="M6.6 10.8a15.1 15.1 0 0 0 6.6 6.6l2.2-2.2c.3-.3.7-.4 1-.2 1.1.4 2.3.6 3.6.6.6 0 1 .4 1 1V20c0 .6-.4 1-1 1A17 17 0 0 1 3 4c0-.6.4-1 1-1h3.5c.6 0 1 .4 1 1 0 1.3.2 2.5.6 3.6.1.3 0 .7-.2 1z"/></svg></span>
    <span><b>CALL US</b><strong>555.014.2290</strong></span>
  </div>
  <div class="f-item" style="left:75px;top:98px">
    <span class="ic"><svg width="9" height="7" viewBox="0 0 17 13"><rect width="17" height="13" rx="1.5" fill="#fff"/><path d="M1 1.5l7.5 6 7.5-6" fill="none" stroke="#2694a9" stroke-width="1.6"/></svg></span>
    <span><b>E MAIL US</b><strong>info@albayanacademy.com</strong></span>
  </div>

  <div class="frame"></div>
  <div class="frame-gap"></div>
  <div class="brand-foot">AL-BAYAN<small>ARABIC ACADEMY</small></div>

  <nav class="f-links"><span>HOME</span><span>ABOUT US</span><span>OUR COURSES</span><span>CONTACT US</span></nav>

  <h3 style="left:512px;top:33px">FOLLOW US</h3>
  <div class="f-item" style="left:511px;top:63px"><span class="ic"></span><span>Like us on<br>OUR PAGE</span></div>
  <div class="f-item" style="left:511px;top:102px"><span class="ic"></span><span>Follow us on<br>NEWS FEED</span></div>
  <div class="f-item" style="left:511px;top:141px"><span class="ic"></span><span>Follow us on<br>NETWORK</span></div>

  <div class="f-line"></div>
  <p class="copy">Copyright © 2020 All Rights Reserved</p>
</footer>

</body>
</html>
```